Brightwell Aero Services Logo

I need a website and logo for the parent company Brightwell Aero Services, which encompasses general aviation aircraft repair, small aircrat rental and flight school. The company is based in Marrowfield, Ohio at the Tolleson county airport. A saying that can be incorporated somehere could be, "Quality flying is safe flying", "Safety in mind is no accident" ,. I need a website and logo.

The company started as a repair shop performing repairs and inspections on Harlan, Vantor, Delkin and Ralstead general aviation aircraft, all models of single engine piston, multi engine piston, and single engine turboprop with an emphasis on Harlan Solvane and AeroTurn turbo prop aircraft. We have se=ince entered the aircraft rental and flight instruction market using the Delkin 240 ang Harlan Ranger aircraft.

Number of Pages; I don't know. Maybe 5 ? A home page for Brightwell Aero Services, page for maintenance and repairs and a couple for the rental and school. The maintenance shop is busy, always has been. I need to get the rental and school advertised and busy.

I have a logo for the maintenance shop shirts, not for the school. I do not have the file. I paid a business locally to do that and print on the shirts. They have the file.

Target Market(s)

In our flight school rental fleet department, we are looking for persons wishing to obtain their private pilot license and continuing on into their commercial and instrument ratings. In the aircraft maintenance department, we are looking for new customers who want a better and more quality relationship with their aircraft maintenance provider who will give more detail and quality in the repairs with an emphasis on safety and fewer problems between scheduled maintenance cycles on their aircraft. Brightwell's owner, Dale Hutchins, has been performing aircraft maintenance in the Atlanta area for 27 years. He has built a steady customer base through those years.

```html
<!DOCTYPE html>
<html lang="en">
<head>
<meta charset="utf-8">
<title>Brightwell Aero Services</title>
<link rel="stylesheet" href="https://fonts.googleapis.com/css2?family=Oswald:wght@300;400&family=Roboto+Condensed:wght@400&family=Mulish:wght@400;600&display=swap">
<style>
:root{
  --navy:#1c45a3;
  --heading:#1b4a86;
  --teal:#2497bd;
  --teal-light:#cfe5ea;
  --panel:#efefef;
  --section-grey:#f0f0f0;
  --text:#555;
  --dark:#333;
  --footer:#000;
  --white:#fff;
}
*{margin:0;padding:0;box-sizing:border-box}
html,body{width:1200px;height:4317px;overflow:hidden}
body{position:relative;background:var(--white);font-family:"Mulish",sans-serif;color:var(--text)}
.abs{position:absolute}
.heading{font-family:"Roboto Condensed",sans-serif;font-weight:400;color:var(--heading)}
.rule{position:absolute;height:3px;width:50px;background:var(--teal)}
.btn{position:absolute;display:flex;align-items:center;justify-content:center;background:var(--teal);color:var(--white);font-family:"Oswald",sans-serif;font-weight:300;font-size:12px;letter-spacing:.3px;text-transform:uppercase}
.photo{position:absolute}
p.body{font-size:13px;line-height:23px;color:var(--text)}

/* top bar */
.topbar{left:0;top:0;width:1200px;height:45px;background:var(--navy)}
.social{left:163px;top:15px;display:flex;gap:12px}
.social span{width:14px;height:14px;border-radius:50%;background:var(--white)}
.call{right:161px;top:12px;color:var(--white);font-size:13px;display:flex;align-items:center;gap:8px}
.call b{font-weight:600}

/* hero */
.hero-photo{left:0;top:45px;width:1200px;height:650px;background:linear-gradient(110deg,#3b3d40 0%,#5d6166 35%,#b9bcc0 55%,#d9dadc 65%,#4c4f52 85%,#2d2f31 100%)}
.hero-shape{left:0;top:45px}
.brand{left:163px;top:62px;color:var(--white);font-family:"Oswald",sans-serif;font-weight:400;font-size:26px;line-height:28px;width:270px}
.nav{left:509px;top:73px;display:flex;gap:28px;font-family:"Oswald",sans-serif;font-weight:300;font-size:14px;color:var(--white);text-transform:uppercase}
.hero-title{left:163px;top:246px;width:480px;color:var(--white);font-family:"Oswald",sans-serif;font-weight:300;font-size:52px;line-height:64px}
.hero-btn{left:163px;top:394px;width:139px;height:42px;border-radius:8px;background:var(--navy);font-family:"Mulish",sans-serif;font-size:15px;letter-spacing:.5px;font-weight:400}

/* services */
.section-title{left:0;width:1200px;text-align:center;font-size:34px}
.card{position:absolute;top:866px;width:278px}
.card .photo{position:relative;width:278px;height:232px}
.card h3{font-family:"Roboto Condensed",sans-serif;font-weight:400;font-size:17px;color:var(--dark);margin:17px 0 0 0}
.card .plus{position:absolute;right:18px;top:283px;width:22px;height:22px}
.card-active{left:147px;top:878px;width:277px;height:320px;border:2px solid var(--teal)}
.card p{font-size:12.5px;line-height:19px;color:var(--dark);margin-top:4px}

/* split sections */
.panel{left:521px;width:679px;background:var(--panel)}
.accent-block{width:104px;height:14px;background:var(--heading)}
.accent-line{height:2px;width:121px;background:var(--teal)}
.split-title{left:625px;font-size:31px;line-height:34px}
.split-text{left:625px;width:420px}

/* reviews */
.reviews{left:0;top:1889px;width:1200px;height:526px;background:var(--section-grey)}
.review{position:absolute;top:2117px;width:426px;height:199px;background:var(--white);text-align:center}
.review .bar{position:absolute;left:17px;bottom:-8px;width:392px;height:8px;background:var(--teal-light)}
.avatar{position:absolute;top:-44px;left:169px;width:88px;height:88px;border-radius:50%;border:3px solid var(--teal);background:#d9d9d9;overflow:hidden}
.avatar i{position:absolute;inset:5px;border-radius:50%;background:linear-gradient(#b9a898,#6f5d50)}
.review h4{font-family:"Roboto Condensed",sans-serif;font-weight:400;color:var(--heading);font-size:17px;margin-top:58px}
.review p{font-size:12.5px;line-height:23px;color:var(--dark);margin:10px 20px 0}
.arrow{width:40px;height:40px;border-radius:50%;background:var(--white);display:flex;align-items:center;justify-content:center}

/* rental */
.rental-photo{left:0;top:3030px;width:1200px;height:607px;background:linear-gradient(180deg,#a9c3ea 0%,#bed2ee 55%,#7f9877 63%,#6e9a4a 75%,#5e8c3c 100%)}
.rental-panel{left:161px;top:3121px;width:496px;height:427px;background:var(--panel)}
.checks{list-style:none;font-size:12.5px;color:var(--text)}
.checks li{display:flex;align-items:center;gap:7px;height:27px}

/* cta */
.cta-title{left:0;top:3718px;width:1200px;text-align:center;font-size:31px}
.cta-text{left:210px;top:3772px;width:780px;text-align:center;font-size:15px;line-height:28px;color:var(--text)}

/* footer */
.footer{left:0;top:3930px;width:1200px;height:387px;background:var(--footer);color:var(--white)}
.footer h5{font-family:"Oswald",sans-serif;font-weight:400;font-size:17px;letter-spacing:.2px}
.links{list-style:none;font-size:12.5px}
.links li{height:35px;display:flex;align-items:center;gap:12px}
.contact-item{display:flex;gap:14px;font-size:12.5px;line-height:19px}
.contact-item b{font-weight:600;font-size:14px}
.pin{width:30px;height:30px;border-radius:50%;background:var(--navy);flex:none;display:flex;align-items:center;justify-content:center}
.foot-brand{left:818px;top:4110px;width:240px;text-align:center;font-family:"Oswald",sans-serif;font-weight:400;font-size:28px;line-height:34px;color:var(--white)}
.foot-divider{left:163px;top:4262px;width:876px;height:1px;background:#333}
.copyright{left:0;top:4287px;width:1200px;text-align:center;font-size:13px;color:#ddd}
</style>
</head>
<body>

<!-- top bar -->
<div class="abs topbar"></div>
<div class="abs social" aria-label="Social links"><span></span><span></span><span></span><span></span></div>
<div class="abs call">
  <svg width="22" height="22" viewBox="0 0 22 22"><circle cx="11" cy="11" r="11" fill="#fff"/><path d="M7.5 6c.6-.4 1.2-.2 1.6.4l1 1.6c.3.5.2 1-.2 1.4l-.6.5c.5 1.2 1.4 2.2 2.6 2.7l.5-.6c.4-.4.9-.5 1.4-.2l1.6 1c.6.4.8 1 .4 1.6-.7 1-1.8 1.4-3 .9-2.7-1.1-4.6-3-5.6-5.6-.5-1.1 0-2.2.9-2.9z" fill="#1c45a3"/></svg>
  <span><b>Call Us</b> 123-456-7890</span>
</div>

<!-- hero -->
<div class="abs hero-photo" role="img" aria-label="Photo of a white light aircraft in a maintenance hangar with a mechanic at work"></div>
<svg class="abs hero-shape" width="1200" height="660" viewBox="0 0 1200 660">
  <polygon points="0,508 930,650 1200,516 1200,660 0,660" fill="#fff"/>
  <polygon points="0,508 930,650 1200,516 1200,540 930,668 870,660 0,522" fill="#1c45a3"/>
  <polygon points="0,522 870,660 0,660" fill="#fff"/>
  <polygon points="930,668 1200,540 1200,660 930,660" fill="#fff"/>
</svg>
<div class="abs brand">Brightwell Aero Services</div>
<nav class="abs nav">
  <span>Home</span><span>Maintenance &amp; Repairs</span><span>Aircraft Rental</span><span>Flight School</span><span>Contact Us</span>
</nav>
<h1 class="abs hero-title">"Quality Flying Is Safe Flying"</h1>
<div class="btn hero-btn">CONTACT US</div>

<!-- services -->
<h2 class="abs heading section-title" style="top:775px">OUR SERVICES</h2>
<div class="rule" style="left:575px;top:831px"></div>

<div class="card" style="left:161px">
  <div class="photo" role="img" aria-label="Photo of an instructor and student beside a propeller in a hangar" style="background:linear-gradient(135deg,#5a5f66,#9aa0a6 50%,#3a3c40)"></div>
  <h3 style="margin-left:16px">Flight School</h3>
  <p style="margin-left:16px">Lorem ipsum dolor sit amet,<br>consectetuer adipiscin.</p>
  <svg class="plus" viewBox="0 0 22 22"><path d="M11 2v18M2 11h18" stroke="#444" stroke-width="2"/></svg>
</div>
<div class="abs card-active"></div>

<div class="card" style="left:461px">
  <div class="photo" role="img" aria-label="Photo of a small white and red aircraft parked on a runway" style="background:linear-gradient(180deg,#d9d6d2 0%,#cfcac4 55%,#a49c8e 70%,#8f8878 100%)"></div>
  <h3>Small Aircraft Rental</h3>
  <svg class="plus" style="right:0" viewBox="0 0 22 22"><path d="M11 2v18M2 11h18" stroke="#444" stroke-width="2"/></svg>
</div>

<div class="card" style="left:761px">
  <div class="photo" role="img" aria-label="Photo of several aircraft under repair inside a hangar" style="background:linear-gradient(180deg,#6f7a6f 0%,#9aa59c 40%,#c8ccc8 65%,#5a5a58 100%)"></div>
  <h3>Aircraft Repair</h3>
  <svg class="plus" style="right:0" viewBox="0 0 22 22"><path d="M11 2v18M2 11h18" stroke="#444" stroke-width="2"/></svg>
</div>

<div class="btn" style="left:546px;top:1235px;width:108px;height:37px">CONTACT US</div>

<!-- about -->
<div class="abs panel" style="top:1361px;height:399px"></div>
<div class="abs accent-block" style="left:241px;top:1418px"></div>
<div class="abs accent-line" style="left:72px;top:1504px"></div>
<div class="photo" role="img" aria-label="Photo of a white single engine aircraft taxiing past trees" style="left:161px;top:1431px;width:426px;height:364px;background:linear-gradient(180deg,#2f4a26 0%,#45622f 50%,#6e6f6a 72%,#8a8c86 100%)"></div>
<h2 class="abs heading split-title" style="top:1418px">About<br>Brightwell Aero Services</h2>
<div class="rule" style="left:625px;top:1504px"></div>
<div class="abs split-text" style="top:1522px">
  <p class="body">Lorem ipsum dolor sit amet, consectetur adipiscing elit, sed do eiusmod tempor incididunt ut labore et dolore magna aliqua. Ut enim ad minim veniam quis nostrud.</p>
  <p class="body" style="margin-top:5px">Quis autem vel eum iure reprehenderit qui in ea voluptate velit esse quam nihil molestiae consequatur...</p>
</div>
<div class="btn" style="left:625px;top:1662px;width:99px;height:36px">READ MORE</div>

<!-- reviews -->
<div class="abs reviews"></div>
<h2 class="abs heading section-title" style="top:1977px">CUSTOMER REVIEWS</h2>
<div class="rule" style="left:575px;top:2033px"></div>

<div class="review" style="left:161px">
  <div class="avatar" role="img" aria-label="Portrait of the reviewer"><i></i></div>
  <h4>Colin Averett</h4>
  <p>Lorem ipsum dolor sit amet, consectetur adipiscing elit, sed do eiusmod tempor incididunt ut labore et dolore magna aliqua. Ut enim ad minim veniam Nemo enim ipsam voluptatem quia voluptas sit aspernatur...</p>
  <div class="bar"></div>
</div>
<div class="review" style="left:613px">
  <div class="avatar" role="img" aria-label="Portrait of the reviewer"><i></i></div>
  <h4>Janet Pellow</h4>
  <p>Lorem ipsum dolor sit amet, consectetur adipiscing elit, sed do eiusmod tempor incididunt ut labore et dolore magna aliqua. Ut enim ad minim veniam Nemo enim ipsam voluptatem quia voluptas sit aspernatur...</p>
  <div class="bar"></div>
</div>
<div class="abs arrow" style="left:80px;top:2201px"><svg width="12" height="14" viewBox="0 0 12 14"><path d="M8 2L3 7l5 5" stroke="#222" stroke-width="2.2" fill="none"/></svg></div>
<div class="abs arrow" style="left:1078px;top:2197px"><svg width="12" height="14" viewBox="0 0 12 14"><path d="M4 2l5 5-5 5" stroke="#2497bd" stroke-width="2.2" fill="none"/></svg></div>

<!-- flight schools -->
<div class="abs panel" style="top:2506px;height:397px"></div>
<div class="abs accent-block" style="left:241px;top:2560px"></div>
<div class="abs accent-line" style="left:72px;top:2647px"></div>
<div class="photo" role="img" aria-label="Photo of a pilot seated in the cockpit of a white and blue light aircraft" style="left:161px;top:2574px;width:426px;height:364px;background:linear-gradient(135deg,#8c949c 0%,#d8dde2 45%,#9fa8b2 70%,#5b6470 100%)"></div>
<h2 class="abs heading split-title" style="top:2560px">OUR FLIGHT SCHOOLS</h2>
<div class="rule" style="left:625px;top:2610px"></div>
<div class="abs split-text" style="top:2630px">
  <p class="body">Lorem ipsum dolor sit amet, consectetur adipiscing elit Nunc vulputate eleifend mi, sit amet semper urna acsan at.</p>
  <p class="body" style="margin-top:10px">Lorem ipsum dolor sit amet, consectetuer adipiscing elit, sed diam nonummy nibh euismod tincidunt ut laoreet dor magna aliquam erat volutpat. Ut wisi enim ad minim ve quis nostrud exerci tation ullamcorper quis nostrud suscipit...</p>
</div>
<div class="btn" style="left:625px;top:2809px;width:99px;height:36px">READ MORE</div>

<!-- flight rental -->
<div class="abs rental-photo" role="img" aria-label="Photo of a white high wing aircraft parked on a grass field under a clear sky"></div>
<div class="abs rental-panel">
  <h2 class="heading" style="position:absolute;left:57px;top:52px;font-size:31px">OUR FLIGHT RENTAL</h2>
  <div class="rule" style="left:57px;top:104px"></div>
  <p class="body" style="position:absolute;left:57px;top:124px;width:400px">Lorem ipsum dolor sit amet, consectetur adipiscing elit Nunc vulputate eleifend mi, sit amet semper urna acsan at.</p>
  <ul class="checks" style="position:absolute;left:57px;top:182px">
    <li><svg width="12" height="12" viewBox="0 0 12 12"><rect x="0.5" y="0.5" width="11" height="11" rx="2" fill="none" stroke="#2497bd"/><path d="M3 6l2 2 4-4" stroke="#2497bd" stroke-width="1.6" fill="none"/></svg>Lorem ipsum dolor sit amet consectetur adipiscing.</li>
    <li><svg width="12" height="12" viewBox="0 0 12 12"><rect x="0.5" y="0.5" width="11" height="11" rx="2" fill="none" stroke="#2497bd"/><path d="M3 6l2 2 4-4" stroke="#2497bd" stroke-width="1.6" fill="none"/></svg>Ut enim ad minim veniam quis nostrud semper.</li>
    <li><svg width="12" height="12" viewBox="0 0 12 12"><rect x="0.5" y="0.5" width="11" height="11" rx="2" fill="none" stroke="#2497bd"/><path d="M3 6l2 2 4-4" stroke="#2497bd" stroke-width="1.6" fill="none"/></svg>laboris nisi ut aliquip ex ea commodo consequat.</li>
    <li><svg width="12" height="12" viewBox="0 0 12 12"><rect x="0.5" y="0.5" width="11" height="11" rx="2" fill="none" stroke="#2497bd"/><path d="M3 6l2 2 4-4" stroke="#2497bd" stroke-width="1.6" fill="none"/></svg>Duis aute irure dolor in reprehenderit involuptate.</li>
    <li><svg width="12" height="12" viewBox="0 0 12 12"><rect x="0.5" y="0.5" width="11" height="11" rx="2" fill="none" stroke="#2497bd"/><path d="M3 6l2 2 4-4" stroke="#2497bd" stroke-width="1.6" fill="none"/></svg>Nostrum exercitationem ullam corporis.</li>
  </ul>
  <div class="btn" style="left:57px;top:332px;width:117px;height:35px;gap:5px">
    <svg width="11" height="11" viewBox="0 0 11 11"><rect x="0.5" y="1.5" width="10" height="9" fill="none" stroke="#fff"/><path d="M0.5 4h10M3 0v3M8 0v3" stroke="#fff"/></svg>BOOK NOW
  </div>
</div>

<!-- call to action -->
<h2 class="abs heading cta-title">Lorem Ipsum Dolor Sit Amet Conse Ctetur</h2>
<p class="abs cta-text">At vero eos et accusamus et iusto odio dignissimos ducimus qui blanditiis praesentium voluptatum deleniti atque corrupti quos dolores et quas molestias excepturi sint.</p>
<div class="btn" style="left:547px;top:3840px;width:108px;height:35px">CONTACT US</div>

<!-- footer -->
<footer class="abs footer">
  <h5 style="position:absolute;left:163px;top:50px">QUICK LINKS</h5>
  <ul class="links" style="position:absolute;left:163px;top:87px">
    <li><span>›</span>Home</li>
    <li><span>›</span>Services</li>
    <li><span>›</span>Maintenance &amp; Repairs</li>
    <li><span>›</span>Aircraft Rental</li>
    <li><span>›</span>Flight School</li>
    <li><span>›</span>Contact Us</li>
  </ul>
  <h5 style="position:absolute;left:466px;top:50px">CONTACT DETAILS</h5>
  <div style="position:absolute;left:466px;top:96px;display:flex;flex-direction:column;gap:22px">
    <div class="contact-item"><span class="pin"><svg width="12" height="14" viewBox="0 0 12 14"><path d="M6 0a5 5 0 0 1 5 5c0 3.5-5 9-5 9S1 8.5 1 5a5 5 0 0 1 5-5z" fill="#fff"/><circle cx="6" cy="5" r="2" fill="#1c45a3"/></svg></span><div><b>Address</b><br>12 Lorem Imsum, Street Name,<br>Marrowfield, Ohio</div></div>
    <div class="contact-item"><span class="pin"><svg width="14" height="14" viewBox="0 0 22 22"><path d="M5 3c1-.6 2-.3 2.6.6l1.6 2.6c.5.8.3 1.6-.3 2.2l-1 .8c.8 2 2.3 3.5 4.2 4.3l.8-1c.6-.6 1.5-.8 2.2-.3l2.6 1.6c1 .6 1.2 1.6.6 2.6-1.1 1.6-2.9 2.2-4.8 1.4C9.2 15.1 6.1 12 4.5 7.8 3.7 6 4.3 4.1 5 3z" fill="#fff"/></svg></span><div><b>Phone</b><br>123.456.7890</div></div>
    <div class="contact-item"><span class="pin"><svg width="14" height="10" viewBox="0 0 14 10"><rect width="14" height="10" fill="#fff"/><path d="M0 0l7 5 7-5" stroke="#1c45a3" fill="none"/></svg></span><div><b>Email</b><br>inquiry@brightwellaero.com</div></div>
  </div>
</footer>
<div class="abs foot-brand">Brightwell<br>Aero Services</div>
<div class="abs foot-divider"></div>
<div class="abs copyright">© 2023 Brightwell Aero Services. All Rights Reserved.</div>

</body>
</html>
```